Web Design Project

We are an online tax Continuing education provider. We provide online courses for tax preparers. We want the front end page to be user friendly and for the buyer to know exactly what they are looking at. We want a front end page to look smiliar www.larkvalefiling.com. It should have a similar feel to this one.
Our website address will be www.7782QX.com
We currently have another website that is www.LedgrUMs.com but we do not want it to look like this. We want a different look but same information.
We have a logo already which is attached. We don't have specific colors in mind for the front page but don't want it to be too busy looking. It should stand out but not too simple either.
Target Market(s)
Tax Preparers. More serious and professional but these folks are usually not tech savy. Simple, easy to use, and functional is key.
Industry/Entity Type
Education
Requirements
Must have
- Use standard HTML & CSS. NO other coding is needed.
We are looking for 5-7 pages including Home page, log in, FAQ.
Please look at our current website www.LedgrUMs.com and also www.larkvalefiling.com

```html
<!DOCTYPE html>
<html lang="en">
<head>
<meta charset="utf-8">
<title>7782QX – Continuing Education Made Simple</title>
<link rel="stylesheet" href="https://fonts.googleapis.com/css2?family=Roboto+Condensed:ital,wght@0,400;0,700;1,700&family=Roboto:wght@400;700&display=swap">
<style>
:root{
  --blue:#1570c0;
  --blue-dark:#0d5aa0;
  --cyan:#1aa2ea;
  --green:#8cb81e;
  --green-dark:#6f9a12;
  --ink:#1d1d1d;
  --muted:#555;
  --line:#dadada;
  --page:#f4f4f4;
  --footer:#dedede;
}
*{box-sizing:border-box;margin:0;padding:0}
html,body{width:758px;height:1200px;overflow:hidden}
body{position:relative;background:var(--page);font-family:Roboto,Arial,sans-serif;color:var(--ink)}
.abs{position:absolute}
.cond{font-family:"Roboto Condensed","Arial Narrow",sans-serif}

/* header */
.header{position:absolute;left:0;top:0;width:758px;height:113px;background:#fff}
.header-band{position:absolute;left:0;top:0}
.header-rule{position:absolute;left:0;top:107px;width:758px;height:5px;background:#e6e9ec}
.brand{position:absolute;left:84px;top:38px;display:flex;align-items:center;gap:8px;font-family:"Roboto Condensed",sans-serif;font-weight:700;font-size:30px;color:#fff}
.brand-dot{width:18px;height:18px;border-radius:50%;background:#fff}
.phone{position:absolute;left:532px;top:15px;display:flex;align-items:center;gap:9px;color:var(--blue);font-family:"Roboto Condensed",sans-serif;font-size:16px;font-weight:700}
.phone-icon{width:21px;height:21px;border-radius:50%;background:#e4e8ec;display:flex;align-items:center;justify-content:center}
.nav{position:absolute;left:450px;top:46px;width:232px;height:24px;background:var(--blue);border-radius:0 12px 12px 0;display:flex;align-items:center;padding-left:11px;gap:0}
.nav a{color:#fff;text-decoration:none;font-family:"Roboto Condensed",sans-serif;font-weight:700;font-size:8.5px;margin-right:15px}
.social{position:absolute;top:82px;width:20px;height:20px;border-radius:50%}

/* hero */
.hero{position:absolute;left:78px;top:120px;width:602px;height:224px;background:linear-gradient(100deg,#6d7f9a 0%,#b7a9a0 30%,#d9c7b5 48%,#8a6a86 62%,#4d5666 80%,#9aa3ad 100%);box-shadow:0 0 0 3px #fff,0 1px 4px 3px rgba(0,0,0,.12)}
.hero-caption{position:absolute;left:295px;top:152px;color:#fff;font-size:17px;font-weight:700;text-shadow:0 1px 3px rgba(0,0,0,.6)}
.hero-dots{position:absolute;left:554px;top:204px;display:flex;gap:5px}
.hero-dots span{width:8px;height:8px;border-radius:50%;background:#fff}
.hero-dots span.on{background:var(--blue);box-shadow:0 0 0 1.5px #fff}

/* feature cards */
.card{position:absolute;top:356px;width:189px;height:176px;background:linear-gradient(#f0f0f0,#fff 40%);border:1px solid #ddd;text-align:center}
.card h2{font-family:"Roboto Condensed",sans-serif;font-weight:400;font-size:15px;line-height:18px;margin-top:14px;color:#222}
.card .thumb{width:107px;height:63px;margin:14px auto 0}
.card p{font-family:"Roboto Condensed",sans-serif;font-size:8px;line-height:10.5px;text-align:left;padding:0 11px;margin-top:17px}
.card p .hl{color:var(--blue)}
.card p .warn{color:#d21;font-weight:700}

.testimonial{position:absolute;left:75px;top:564px;width:607px;height:72px;background:#fff;border-top:1px solid var(--line)}
.testimonial q{position:absolute;left:0;top:18px;width:607px;text-align:center;font-family:"Roboto Condensed",sans-serif;font-style:italic;font-weight:700;font-size:10px;line-height:13px;quotes:none}
.testimonial .by{position:absolute;right:37px;top:54px;font-family:"Roboto Condensed",sans-serif;font-weight:700;font-size:8px;color:var(--blue)}
.rule{position:absolute;left:75px;width:607px;height:1px;background:var(--line)}

/* packages */
.acc-bar{position:absolute;left:75px;width:607px;height:27px;background:linear-gradient(var(--green),var(--green-dark));border-radius:2px;color:#fff;font-family:"Roboto Condensed",sans-serif;font-weight:700;font-size:12px;line-height:27px;padding-left:13px}
.acc-bar .chev{position:absolute;right:7px;top:6px;width:15px;height:15px;border-radius:50%;background:#fff}
.acc-panel{position:absolute;left:75px;top:697px;width:607px;height:207px;background:#fff;border:1px solid #d6d6d6;border-top:none}
.promo{position:absolute;left:7px;top:17px;width:138px;height:176px;background:radial-gradient(circle at 40% 30%,#3dbaf5,#1592d8 70%);color:#fff;text-align:center;font-family:"Roboto Condensed",sans-serif;font-weight:700}
.promo .big{font-size:14px;line-height:19px;margin-top:34px}
.promo .small{font-size:8.5px;margin-top:5px}
.promo .price{font-size:18px;margin-top:2px}
.promo .by{font-size:7.5px;margin-top:9px}
.promo .cta{font-size:10px;margin-top:26px;color:#1b2a3a}
.pkg-head{position:absolute;font-family:"Roboto Condensed",sans-serif;font-weight:700;font-size:9px;color:var(--blue)}
.topic{position:absolute;font-size:7.2px;color:#333}
.topic::before{content:"›";color:var(--green);font-weight:700;margin-right:6px;font-size:9px}
.info{position:absolute;left:158px;width:440px;font-size:7px;color:#333;line-height:15px}

/* footer info */
.about-l{position:absolute;left:78px;top:1007px;width:296px;font-size:8.2px;line-height:11.5px;color:#222}
.about-r{position:absolute;left:385px;top:1001px;width:300px;font-size:8.2px;color:#222}
.about-r ul{list-style:none;font-size:7px;line-height:11.4px;margin-top:11px}
.vline{position:absolute;left:379px;top:992px;width:1px;height:96px;background:var(--line)}
.irs-link{position:absolute;left:78px;top:1106px;font-family:"Roboto Condensed",sans-serif;font-weight:700;font-size:8px}
.btn{position:absolute;left:394px;top:1094px;width:226px;height:24px;background:var(--cyan);color:#fff;font-family:"Roboto Condensed",sans-serif;font-weight:700;font-size:11px;line-height:24px;text-align:center}

.footer{position:absolute;left:0;top:1142px;width:758px;height:58px;background:var(--footer)}
.copy{position:absolute;left:81px;top:23px;font-size:7px;color:#222}
.badge{position:absolute;left:547px;top:12px;width:31px;height:32px;border:2px solid #b0a88a;background:#e8e6df}
.badge-text{position:absolute;left:583px;top:15px;font-size:7.5px;line-height:9px;color:#8a8a8a}
</style>
</head>
<body>

<header class="header">
  <svg class="header-band" width="470" height="113" viewBox="0 0 470 113"><polygon points="0,0 466,0 424,113 0,113" fill="#1570c0"/></svg>
  <div class="header-rule"></div>
  <div class="brand"><span class="brand-dot"></span>7782QX</div>
  <div class="phone">
    <span class="phone-icon"><svg width="12" height="10" viewBox="0 0 12 10"><path d="M1 3c0-2 10-2 10 0v1H8V3H4v1H1z M3 5h6l1 4H2z" fill="#1570c0"/></svg></span>
    800-555-0142
  </div>
  <nav class="nav"><a href="#">HOME</a><a href="#">COURSES</a><a href="#">FAQ</a><a href="#">CONTACT</a><a href="#">SIGN IN</a></nav>
  <span class="social" style="left:577px;background:#2d4f8f"></span>
  <span class="social" style="left:603px;background:#1e94d6"></span>
  <span class="social" style="left:628px;background:#1769a8"></span>
  <span class="social" style="left:653px;background:#f27b21"></span>
</header>

<section class="hero" role="img" aria-label="Photo of smiling students holding books and laptops outdoors">
  <div class="hero-caption cond">CONTINUING EDUCATION MADE SIMPLE!</div>
  <div class="hero-dots"><span class="on"></span><span></span><span></span></div>
</section>

<article class="card" style="left:81px">
  <h2>IRS APPROVED<br>PROVIDER</h2>
  <div class="thumb" style="background:#15206a" role="img" aria-label="Approved provider emblem"></div>
  <p><span class="hl">Click here</span> to see our approved provider link at IRS website</p>
</article>
<article class="card" style="left:283px">
  <h2>COURSE COMPLETION<br>CERTIFICATE</h2>
  <div class="thumb" style="background:#f4f2fa;border:3px solid #5860a8" role="img" aria-label="Sample certificate of completion"></div>
  <p><span class="warn">IMPORTANT!</span> All federal tax return preparers must have a current year PTIN. Click Here to Renew or Sign up Now!</p>
</article>
<article class="card" style="left:485px">
  <h2>GET<br>PROFESSIONAL</h2>
  <div class="thumb" style="background:linear-gradient(#d6eefc,#4aa8e6)" role="img" aria-label="Silhouettes of business professionals"></div>
  <p>Complete your continuing education require-ments now so you can concentrate on servicing your tax clients.</p>
</article>

<section class="testimonial">
  <q>The class was very convenient because I work crazy hours ... the pace was great. I learned some laws that I wasn't aware of<br>to help my clients. I highly recommend this course to others. Thank you!!</q>
  <span class="by">-Dana.Tx</span>
</section>
<div class="rule" style="top:646px"></div>

<div class="acc-bar" style="top:670px">15-Hour CE Package Only $42 - Click for details<span class="chev"></span></div>
<section class="acc-panel">
  <div class="promo">
    <div class="big">15 HOURS<br>PACKAGES FOR IRS</div>
    <div class="small">REGISTERED TAX PREPARER &nbsp;CE</div>
    <div class="price">$42</div>
    <div class="by">PROVIDED BY 7782QX EDUCATION,LLC</div>
    <div class="cta">CLICK HERE ▸</div>
  </div>
  <div class="pkg-head" style="left:159px;top:18px">15-HOUR PACKAGE FOR IRS REGISTERED TAX-PREPARER CONTINUING EDUCATION:</div>
  <div class="topic" style="left:159px;top:46px">Ethics (2 hrs CE Credit)</div>
  <div class="topic" style="left:159px;top:65px">Earned Income Credit (2 hrs CE Credit)</div>
  <div class="topic" style="left:159px;top:84px">Employee Health Benefits (1 hr CE Credit)</div>
  <div class="topic" style="left:380px;top:46px">Charitable Contributions 101 (3 hrs CE Credit)</div>
  <div class="topic" style="left:380px;top:65px">Deducting Transportation Expenses (2 hrs CE Credit)</div>
  <div class="topic" style="left:380px;top:84px">Federal Tax Law Updates 2012 (3 hrs CE Credit)</div>
  <div class="pkg-head" style="left:158px;top:108px">MORE INFORMATION ABOUT 15-HOUR CE PACKAGE:</div>
  <div class="info" style="top:121px">
    Course Format - immediately downloadable PDF file<br>
    Quiz (Open book) - 70% passing rate required. Take as many times as needed. Average of 15 questions.<br>
    Reporting - Completed CE hours are directly submitted to the IRS within 24 hours.<br>
    Certificate - As soon as CE hours are successfully completed, a certificate will be emailed to you. Per IRS standards, the certificate<br>
    will be available for you to download for 4 years.
  </div>
</section>
<div class="acc-bar" style="top:904px">RTRP Test Simulator Package Only $79.90 - Click for details<span class="chev"></span></div>
<div class="acc-bar" style="top:933px">Combo Package Only $99.90 -- Click for details<span class="chev"></span></div>

<div class="rule" style="top:986px"></div>
<div class="about-l">
  We are your official source for IRS Registered Tax Preparer CE training. Our prices are reasonable, and our courses will help you better understand taxes in an efficient manner.<br><br>
  Quality courses that fulfill IRS registered tax-preparer requirements.
</div>
<div class="vline"></div>
<div class="about-r">
  We are your official source for registered tax-preparer continuing education.
  <ul>
    <li>IRS-approved provider ( Provider Id 4QKRT).</li>
    <li>Easy to understand</li>
    <li>Relevant, up-to-date materials</li>
    <li>Printable Certificate of Completion</li>
    <li>We report CE hours directly to IRS after completion</li>
  </ul>
</div>
<div class="rule" style="top:1088px"></div>
<div class="irs-link">IRS LATEST INFORMATION LINK ( CLICK BUTTON TO OPEN IRS DOCUMENT OR LINK)</div>
<a class="btn">RTRP TEST CANDIDATE INFORAMTIONS</a>
<div class="rule" style="top:1126px"></div>

<footer class="footer">
  <div class="copy">Copyright © 2013, All rights reserved.</div>
  <div class="badge"></div>
  <div class="badge-text">APPROVED<br>CONTINUING EDUCATION<br>ACCREDITOR</div>
</footer>

</body>
</html>
```